QVR business card

Need a business card for a company that provides instructional design and elearning development services. The website is here: http://quorvane.studio/

I'm attaching a current logo, as well as the old business card design. While I like to keep it clean, the old design is too simplistic for my liking. The only idea I want to reuse from the old design is placing industry jargon on the back of the card, just need a better way to present it. But if you have other ideas for the back--feel free to experiment.

Please use the colors complementary to the color we have on the website. Thank you!

```html
<!DOCTYPE html>
<html lang="en">
<head>
<meta charset="utf-8">
<title>QVR business card</title>
<link rel="stylesheet" href="https://fonts.googleapis.com/css2?family=Source+Sans+3:wght@400;600;700&display=swap">
<style>
  :root {
    --stage: #000000;
    --card-light: #f3f3f3;
    --teal: #2aada7;
    --teal-deep: #22a19b;
    --ink: #1d1d1d;
    --white: #ffffff;
  }
  * { margin: 0; padding: 0; box-sizing: border-box; }
  html, body { width: 1200px; height: 900px; overflow: hidden; background: var(--stage); }
  body { position: relative; font-family: "Source Sans 3", "Myriad Pro", sans-serif; }

  .card { position: absolute; top: 200px; width: 310px; height: 502px; overflow: hidden; }
  .card--front { left: 265px; background: var(--card-light); border-radius: 56px 0 56px 0; }
  .card--back { left: 641px; width: 309px; border-radius: 0 56px 0 56px;
    background: linear-gradient(160deg, var(--teal-deep) 0%, var(--teal) 100%); }

  .brand-name { position: absolute; left: 0; right: 0; text-align: center;
    font-weight: 700; letter-spacing: 2px; line-height: 1; }
  .card--front .brand-name { top: 92px; font-size: 72px; color: var(--teal); }
  .card--back .brand-name { top: 42px; font-size: 68px; color: var(--white); }

  .holder-name { position: absolute; left: 27px; top: 363px; font-size: 18px;
    font-weight: 600; color: var(--teal); }
  .contact-list { position: absolute; left: 27px; top: 402px; list-style: none; }
  .contact-list li { display: flex; align-items: center; height: 18px;
    font-size: 14.5px; color: var(--ink); }
  .contact-list svg { width: 10px; height: 10px; margin-right: 6px; flex: none; }

  .help-title { position: absolute; left: 26px; top: 258px; font-size: 19.5px;
    font-weight: 600; color: var(--white); letter-spacing: 0.2px; }
  .service-list { position: absolute; left: 26px; top: 298px; list-style: none; }
  .service-list li { display: flex; align-items: center; height: 26.3px;
    font-size: 14.5px; font-weight: 600; color: var(--white); }
  .service-list li::before { content: ""; width: 8px; height: 8px; border-radius: 50%;
    background: var(--white); margin: 0 19px 0 2px; flex: none; }
</style>
</head>
<body>
  <section class="card card--front" aria-label="Card front">
    <div class="brand-name">QVR</div>
    <h2 class="holder-name">Marek Ostrowin</h2>
    <ul class="contact-list">
      <li>
        <svg viewBox="0 0 10 10" aria-hidden="true"><path d="M2 0.5 L3.6 2.6 L2.7 3.6 Q3.6 5.8 6.2 7.2 L7.3 6.3 L9.5 7.9 L8.3 9.5 Q1.5 8 0.5 1.6 Z" fill="var(--teal)"/></svg>
        555-014-2871
      </li>
      <li>
        <svg viewBox="0 0 10 10" aria-hidden="true"><rect x="0.5" y="2" width="9" height="6.5" fill="var(--teal)"/><path d="M0.8 2.3 L5 5.6 L9.2 2.3" stroke="var(--card-light)" stroke-width="0.9" fill="none"/></svg>
        mostrowin@quorvane.studio
      </li>
      <li>
        <svg viewBox="0 0 10 10" aria-hidden="true"><circle cx="5" cy="5" r="4.5" fill="var(--teal)"/><path d="M0.5 5 H9.5 M5 0.5 Q2.6 5 5 9.5 M5 0.5 Q7.4 5 5 9.5" stroke="var(--card-light)" stroke-width="0.6" fill="none"/></svg>
        www.quorvane.studio
      </li>
    </ul>
  </section>

  <section class="card card--back" aria-label="Card back">
    <div class="brand-name">QVR</div>
    <h2 class="help-title">HOW CAN WE HELP?</h2>
    <ul class="service-list">
      <li>Mobile Learning Scorm</li>
      <li>Instuctional Design Lms</li>
      <li>Moocs Elearning Html5</li>
      <li>Adult Learning Theory</li>
      <li>Gamification Classroom</li>
      <li>Xapi Blended Learning</li>
    </ul>
  </section>
</body>
</html>
```